Business Card Design

WE are looking for a premium quality Business Cards for a Law Firm . Copies of our current business card is attached.

Contact Information for Business Card

xyz

```html
<!DOCTYPE html>
<html lang="en">
<head>
<meta charset="utf-8">
<title>Ashcombe Lawyers – Business Cards</title>
<link rel="stylesheet" href="https://fonts.googleapis.com/css2?family=Tinos:wght@400;700&display=swap">
<style>
  :root {
    --gold: #cdab68;
    --green: #0f2a1c;
    --cream: #f4ead2;
    --white: #ffffff;
    --ink: #121212;
    --backdrop: #e7e5e1;
  }
  * { box-sizing: border-box; margin: 0; padding: 0; }
  html, body { width: 1200px; height: 780px; overflow: hidden; }
  body {
    background: var(--backdrop);
    font-family: "Tinos", "Times New Roman", serif;
    font-weight: 700;
    position: relative;
  }
  .card {
    position: absolute;
    top: 220px;
    width: 560px;
    height: 340px;
    border-radius: 18px;
    overflow: hidden;
  }
  /* ---------- Back card ---------- */
  .card-back { left: 25px; background: var(--gold); color: var(--green); }
  .brand { position: absolute; display: flex; align-items: center; gap: 12px; }
  .brand-mark { border-radius: 50%; border: 4px solid currentColor; flex: none; }
  .brand-name { line-height: 1.05; }
  .brand-name span { display: block; }
  .card-back .brand { left: 150px; top: 34px; }
  .card-back .brand-mark { width: 58px; height: 58px; }
  .card-back .brand-name { font-size: 34px; letter-spacing: 1px; }
  .card-back .brand-name span + span { font-size: 16px; letter-spacing: 9px; }

  .tagline-band {
    position: absolute;
    left: 0; right: 0; top: 150px;
    height: 30px;
    background: var(--green);
    color: var(--cream);
    font-size: 15px;
    letter-spacing: 1px;
    display: flex; align-items: center; justify-content: center;
  }
  .offices {
    position: absolute;
    left: 0; right: 0; top: 196px; bottom: 22px;
    display: flex;
  }
  .office {
    flex: 1;
    padding: 8px 14px 0;
    text-align: center;
    font-size: 12.5px;
    line-height: 1.45;
  }
  .office + .office { border-left: 1.5px solid var(--cream); }
  .office-city {
    font-size: 17px;
    letter-spacing: 1px;
    display: inline-block;
    border-bottom: 1.5px solid var(--green);
    margin-bottom: 4px;
  }
  .office-phone { display: inline-flex; align-items: center; gap: 5px; }
  .icon { width: 12px; height: 12px; flex: none; }

  /* ---------- Front card ---------- */
  .card-front { left: 615px; background: var(--white); color: var(--ink); }
  .card-front .brand { right: 30px; top: 40px; color: var(--green); flex-direction: column; gap: 8px; }
  .card-front .brand-mark { width: 74px; height: 74px; border-color: var(--gold); border-width: 5px; }
  .card-front .brand-name { font-size: 32px; text-align: center; }
  .card-front .brand-name span + span { font-size: 15px; letter-spacing: 9px; }

  .name-bar { position: absolute; left: 0; top: 90px; width: 12px; height: 58px; background: var(--gold); }
  .person { position: absolute; left: 30px; top: 84px; }
  .person-name { color: var(--gold); font-size: 28px; letter-spacing: 1px; line-height: 1; }
  .person-role { font-size: 15px; line-height: 1.3; margin-top: 6px; }
  .address { position: absolute; left: 40px; top: 166px; font-size: 15px; line-height: 1.3; }
  .contacts { position: absolute; left: 40px; top: 234px; list-style: none; font-size: 14px; line-height: 1.35; }
  .contacts li { display: flex; align-items: center; gap: 8px; }
  .contacts .icon { color: var(--gold); }
  .front-bands { position: absolute; inset: 0; width: 560px; height: 340px; pointer-events: none; }
</style>
</head>
<body>

  <section class="card card-back" aria-label="Business card reverse">
    <div class="brand">
      <div class="brand-mark"></div>
      <div class="brand-name"><span>ASHCOMBE</span><span>LAWYERS</span></div>
    </div>

    <div class="tagline-band">CLEAR COUNSEL. TRUSTED RESULTS. EVERY TIME</div>

    <div class="offices">
      <div class="office">
        <div class="office-city">MELBOURNE</div><br>
        Level 22, 88 Flinders Street,<br>
        MELBOURNE, VIC 3000<br>
        <span class="office-phone">
          <svg class="icon" viewBox="0 0 24 24"><path fill="currentColor" d="M6.6 10.8a15.1 15.1 0 006.6 6.6l2.2-2.2a1 1 0 011-.25 11.4 11.4 0 003.6.57 1 1 0 011 1V20a1 1 0 01-1 1A17 17 0 013 4a1 1 0 011-1h3.5a1 1 0 011 1c0 1.25.2 2.450.57 3.57a1 1 0 01-.25 1z"/></svg>
          +61 03 5550 1836
        </span>
      </div>
      <div class="office">
        <div class="office-city">SYDNEY</div><br>
        Level 12, Riverside House<br>
        45 Church Street<br>
        PARRAMATTA, NSW 2150<br>
        <span class="office-phone">
          <svg class="icon" viewBox="0 0 24 24"><path fill="currentColor" d="M6.6 10.8a15.1 15.1 0 006.6 6.6l2.2-2.2a1 1 0 011-.25 11.4 11.4 0 003.6.57 1 1 0 011 1V20a1 1 0 01-1 1A17 17 0 013 4a1 1 0 011-1h3.5a1 1 0 011 1c0 1.25.2 2.45.57 3.57a1 1 0 01-.25 1z"/></svg>
          +61 02 5550 7421
        </span>
      </div>
      <div class="office">
        <div class="office-city">PERTH</div><br>
        Level 19, Swan Tower<br>
        120 Hay Street<br>
        PERTH, WA 6000<br>
        <span class="office-phone">
          <svg class="icon" viewBox="0 0 24 24"><path fill="currentColor" d="M6.6 10.8a15.1 15.1 0 006.6 6.6l2.2-2.2a1 1 0 011-.25 11.4 11.4 0 003.6.57 1 1 0 011 1V20a1 1 0 01-1 1A17 17 0 013 4a1 1 0 011-1h3.5a1 1 0 011 1c0 1.25.2 2.45.57 3.57a1 1 0 01-.25 1z"/></svg>
          +61 08 5550 3958
        </span>
      </div>
    </div>
  </section>

  <section class="card card-front" aria-label="Business card front">
    <svg class="front-bands" viewBox="0 0 560 340" aria-hidden="true">
      <path fill="var(--gold)" d="M0 340 V322 H350 C372 322 386 314 400 300 L432 300 C412 324 396 340 368 340 Z"/>
      <path fill="var(--green)" d="M402 298 L540 212 Q552 205 560 204 V222 L434 298 Z"/>
    </svg>

    <div class="brand">
      <div class="brand-mark"></div>
      <div class="brand-name"><span>ASHCOMBE</span><span>LAWYERS</span></div>
    </div>

    <div class="name-bar"></div>
    <div class="person">
      <h1 class="person-name">DANIEL MERCER</h1>
      <p class="person-role">Director and Principal Solicitor<br>MBA, Juris Doctor</p>
    </div>

    <p class="address">
      Suite 310, Harlow Chambers,<br>
      215 Little Lonsdale Street,<br>
      Melbourne VIC 3000
    </p>

    <ul class="contacts">
      <li>
        <svg class="icon" viewBox="0 0 24 24"><path fill="currentColor" d="M6.6 10.8a15.1 15.1 0 006.6 6.6l2.2-2.2a1 1 0 011-.25 11.4 11.4 0 003.6.57 1 1 0 011 1V20a1 1 0 01-1 1A17 17 0 013 4a1 1 0 011-1h3.5a1 1 0 011 1c0 1.25.2 2.45.57 3.57a1 1 0 01-.25 1z"/></svg>
        +61 7 3555 0142
      </li>
      <li>
        <svg class="icon" viewBox="0 0 24 24"><rect x="6" y="2" width="12" height="20" rx="2" fill="none" stroke="currentColor" stroke-width="2"/><circle cx="12" cy="18" r="1.2" fill="currentColor"/></svg>
        +61 0400 555 271
      </li>
      <li>
        <svg class="icon" viewBox="0 0 24 24"><circle cx="12" cy="12" r="9" fill="none" stroke="currentColor" stroke-width="2"/><path d="M3 12h18M12 3c3 3 3 15 0 18M12 3c-3 3-3 15 0 18" fill="none" stroke="currentColor" stroke-width="1.6"/></svg>
        www.ashcombelawyers.com.au
      </li>
      <li>
        <svg class="icon" viewBox="0 0 24 24"><rect x="2" y="5" width="20" height="14" rx="2" fill="none" stroke="currentColor" stroke-width="2"/><path d="M3 6l9 7 9-7" fill="none" stroke="currentColor" stroke-width="2"/></svg>
        daniel@ashcombelawyers.com.au
      </li>
    </ul>
  </section>

</body>
</html>
```